Professional Services - letterhead / business cards

The company (velmora partners) will provide services to Investment Funds and large investors in Spain. I have recently chosen a logo that I am attaching.

I would like a simple stationary design that i could use as letter head, business cards and "with compliments" cards.

I am not quite sure which color I will mostly use for the logo, in the email signature I will probably lean towards the white background and grey letters. I am attaching my favourite options.

Target Market(s)

Large Multinationals, Investment funds and Law firms

Industry/Entity Type

Business

Requirements
Must have
• my details are:
Luis R. Abadal
Velmora Partners S.L.
Casa de Torrelumbre
Calle de Vientoalto 27
28014 Madrid
T: +34 (91) 387-2265
M: +34 (646) 819-054
e-mail: labadal@velmorapartners.com

```html
<!DOCTYPE html>
<html lang="en">
<head>
<meta charset="utf-8">
<title>Velmora Partners – Business Cards</title>
<link rel="stylesheet" href="https://fonts.googleapis.com/css2?family=Questrial&display=swap">
<style>
  :root {
    --navy: #1a1a6e;
    --grey-text: #6b6b6b;
    --grey-band: #b8b8bc;
    --badge: #c9c9cc;
    --card: #ffffff;
    --backdrop: #ececec;
    --shadow: rgba(0, 0, 0, 0.18);
  }
  * { margin: 0; padding: 0; box-sizing: border-box; }
  html, body {
    width: 1200px;
    height: 588px;
    overflow: hidden;
    background: var(--backdrop);
    font-family: "Questrial", "Century Gothic", sans-serif;
  }
  .stationery {
    position: relative;
    width: 1200px;
    height: 588px;
  }
  .card {
    position: absolute;
    top: 146px;
    width: 520px;
    height: 297px;
    background: var(--card);
    box-shadow: 0 6px 18px var(--shadow);
    overflow: hidden;
  }
  .card--front { left: 50px; }
  .card--back { left: 630px; }

  /* Front */
  .wordmark {
    color: var(--navy);
    white-space: nowrap;
    letter-spacing: 0.5px;
  }
  .card--front .wordmark {
    position: absolute;
    left: 0;
    right: 0;
    top: 104px;
    text-align: center;
    font-size: 40px;
  }
  .website {
    position: absolute;
    left: 0;
    right: 0;
    top: 172px;
    text-align: center;
    font-size: 13px;
    letter-spacing: 3.5px;
    color: var(--navy);
    font-style: italic;
  }

  /* Back */
  .edge-band {
    position: absolute;
    left: 0;
    top: 0;
    width: 14px;
    height: 100%;
  }
  .card--back .wordmark {
    position: absolute;
    right: 40px;
    top: 52px;
    font-size: 30px;
  }
  .holder {
    position: absolute;
    left: 196px;
    top: 128px;
  }
  .holder__name {
    font-size: 17px;
    letter-spacing: 1px;
    color: var(--navy);
    text-transform: uppercase;
  }
  .holder__company {
    font-size: 11px;
    color: var(--grey-text);
    margin-top: 1px;
  }
  .contact {
    margin-top: 10px;
    font-size: 12px;
    color: var(--grey-text);
    line-height: 18px;
  }
  .contact__row { display: flex; align-items: center; gap: 6px; }
  .contact__gap { width: 14px; }
  .badge {
    display: inline-flex;
    align-items: center;
    justify-content: center;
    width: 14px;
    height: 14px;
    border-radius: 50%;
    background: var(--badge);
    color: #fff;
    font-size: 9px;
  }
  .address {
    margin-top: 12px;
    font-size: 12px;
    color: var(--grey-text);
    line-height: 19px;
  }
</style>
</head>
<body>
<main class="stationery">

  <section class="card card--front" aria-label="Business card front">
    <p class="wordmark">velmora partners</p>
    <p class="website">www.velmorapartners.com</p>
  </section>

  <section class="card card--back" aria-label="Business card back">
    <svg class="edge-band" viewBox="0 0 14 297" preserveAspectRatio="none" aria-hidden="true">
      <rect x="0" y="0" width="14" height="82" fill="var(--navy)"/>
      <rect x="0" y="88" width="14" height="209" fill="var(--grey-band)"/>
    </svg>

    <p class="wordmark">velmora partners</p>

    <div class="holder">
      <p class="holder__name">Luis R. Abadal</p>
      <p class="holder__company">Velmora Partners S.L.</p>

      <div class="contact">
        <p class="contact__row">
          <span class="badge">P</span><span>+34 (91) 387-2265</span>
          <span class="contact__gap"></span>
          <span class="badge">C</span><span>+34 (646) 819-054</span>
        </p>
        <p class="contact__row">
          <span class="badge">E</span><span>labadal@velmorapartners.com</span>
        </p>
      </div>

      <div class="address">
        <p>Casa de Torrelumbre</p>
        <p>Calle de Vientoalto 27, 28014 Madrid</p>
      </div>
    </div>
  </section>

</main>
</body>
</html>
```